Looking for Web Design for NFT project

We are an animal charity company and we are looking for a web designer for our latest NFT project. We need a custom designed single page web site structured in a specific way: about us section, how to buy our nft explanation, roadmap etc. It is strongly required the theme of the website to emphasize the Chinese culture. We insist on this since the animals on the NFTs have chinese descent.

Here are good examples of similar websites in terms of how the web page should be structured:

https://quillfernharbor.com/#/home
https://wobblets.io/
https://tarvelinplay.com/
https://mossgarland.rip/

The structure of our website should be similar to the websites listed above, however, the theme the web page should be original, more playful than serious, colourful, it should be fun and in chinese thematic. The NFTs will be 100x100 pixel 16bit animals.

Target markets: Cryptocurrency and NFT collectors/creators

Target Market(s)

Cryptocurrency and NFT collectors/creators

Industry/Entity Type

NFT Space

Coding

Coded - Design and coding required

Number of Pages Required

1 page

Requirements
Must have
• Chinese thematics / Pekingese dog breed oriented
Nice to have
• The NFTs will be 100x100 pixel pekingese dogs
Should not have
• Anything that is directly related to crypto

```html
<!DOCTYPE html>
<html lang="en">
<head>
<meta charset="utf-8">
<title>Lantern Paws</title>
<link rel="stylesheet" href="https://fonts.googleapis.com/css2?family=Mr+Dafoe&family=Lato:wght@400;700&family=Poppins:wght@400;500;600&display=swap">
<style>
:root{
  --cream:#f9eed0;
  --cream-light:#faf0d6;
  --sand:#e4d8b4;
  --red:#b5000d;
  --red-deep:#bf2a33;
  --pink:#f5b6b7;
  --pink-line:#e38e92;
  --ink:#1f1a17;
  --gold:#f0d49a;
  --white:#ffffff;
}
*{margin:0;padding:0;box-sizing:border-box}
html,body{width:1200px;height:3889px;overflow:hidden}
body{background:var(--cream);font-family:'Lato',sans-serif;color:var(--ink);position:relative}
.abs{position:absolute}
.script{font-family:'Mr Dafoe',cursive;color:var(--red);font-weight:400;line-height:1}
.btn{position:absolute;background:var(--red);color:var(--white);font:700 15px 'Lato',sans-serif;display:flex;align-items:center;justify-content:center;text-transform:uppercase;border-radius:2px}
.art{position:absolute}

/* hero */
.hero{position:absolute;left:0;top:0;width:1200px;height:620px;background:linear-gradient(180deg,var(--cream-light),#f8e9c3)}
.logo{left:115px;top:18px;font-family:'Mr Dafoe',cursive;font-size:44px;color:var(--ink)}
.nav{left:460px;top:30px;display:flex;gap:43px;font-size:15px}
.social{top:38px;display:flex;gap:14px}
.social span{width:13px;height:13px;border-radius:50%;background:var(--red);display:block}
.hero-sub{left:0;top:160px;width:1555px;text-align:center;font-size:58px}
.hero-title{left:0;top:215px;width:1555px;text-align:center;font-size:92px}
.hero-text{left:500px;top:318px;width:555px;text-align:center;font-size:15px;line-height:26px}

/* about */
.about{position:absolute;left:0;top:620px;width:1200px;height:528px;background:var(--cream)}
.section-title{font-size:66px}
.about-text{left:111px;top:172px;width:478px;font-size:15px;line-height:26px;text-align:justify}

/* how to buy */
.buy{position:absolute;left:0;top:1148px;width:1200px;height:515px;background:var(--sand)}
.buy-text{left:220px;top:192px;width:760px;text-align:center;font-size:15px;line-height:26px}

/* roadmap */
.roadmap{position:absolute;left:0;top:1663px;width:1200px;height:1482px}
.rail{position:absolute;width:2px;background:var(--ink)}
.card{position:absolute;background:var(--pink);border:1px solid var(--pink-line);border-radius:2px;width:577px;height:240px;padding:28px 0 0}
.card.right{width:507px}
.diamond{position:absolute;width:14px;height:14px;background:var(--red);transform:rotate(45deg)}
.card .num{position:absolute;font:500 16px 'Poppins',sans-serif;color:var(--red)}
.card h3{position:absolute;font:500 22px/32px 'Poppins',sans-serif;width:380px}
.card p{position:absolute;font-size:14.5px;line-height:26px;width:430px}
.card.flip h3,.card.flip p{text-align:right}

/* faq */
.faq{position:absolute;left:0;top:3145px;width:1200px;height:620px;background:linear-gradient(180deg,#b91f2a,var(--red-deep) 50%,#c8333b)}
.faq-title{left:0;top:55px;width:1200px;text-align:center;font-size:72px;color:var(--white)}
.faq-item{position:absolute;left:230px;width:740px;border:2px solid var(--white);color:var(--white)}
.faq-item h4{position:absolute;left:22px;font:600 25px 'Poppins',sans-serif}
.faq-item .plus{position:absolute;right:46px;font:600 28px 'Poppins',sans-serif}
.faq-item p{position:absolute;left:24px;top:62px;width:590px;font:500 14.5px/26px 'Poppins',sans-serif}

/* footer */
.footer{position:absolute;left:0;top:3765px;width:1200px;height:124px;background:var(--cream);border-top:2px solid #c5202b}
.footer-text{left:110px;top:70px;font-size:15px}
</style>
</head>
<body>

<header class="hero">
  <div class="art" role="img" aria-label="Faint line drawing of a pagoda, mountains and a pine tree" style="left:380px;top:90px;width:820px;height:530px;background:radial-gradient(ellipse at 70% 70%,rgba(240,212,154,.55),rgba(240,212,154,0) 65%)"></div>
  <div class="art" role="img" aria-label="Cherry blossom branch with pink flowers" style="left:0;top:100px;width:510px;height:210px;background:linear-gradient(160deg,rgba(234,90,140,.35),rgba(110,50,30,.25) 55%,rgba(249,238,208,0) 80%)"></div>
  <div class="art" role="img" aria-label="Illustrated Pekingese dog in a golden wave pattern circle" style="left:90px;top:330px;width:285px;height:290px;border-radius:50%;background:radial-gradient(circle at 50% 45%,#b06a40,#e7a45a 60%,#f3c67f)"></div>
  <div class="abs logo">Lantern Paws</div>
  <nav class="abs nav"><span>Home</span><span>About</span><span>How to buy</span><span>Roadmap</span><span>Faq</span></nav>
  <div class="abs social" style="left:980px"><span></span><span></span><span></span><span></span></div>
  <div class="abs script hero-sub">Welcome to</div>
  <h1 class="abs script hero-title">Chinese descent</h1>
  <p class="abs hero-text">Lorem ipsum dolor sit amet, consectetur adipiscing elit, sed do eiusmod tempor incididunt ut labore et dolore magna aliqua.</p>
  <div class="btn" style="left:705px;top:392px;width:148px;height:56px">Get started</div>
</header>

<section class="about">
  <h2 class="abs script section-title" style="left:112px;top:85px">About us</h2>
  <p class="abs about-text">Lorem ipsum dolor sit amet, consectetur adipiscing elit, sed do eiusmod tempor incididunt ut labore et dolore magna aliqua. Ut enim ad minim veniam, quis nostrud exercitation ullamco laboris nisi ut aliquip ex ea commodo consequat. Duis aute irure dolor in reprehenderit in voluptate velit esse cillum dolore eu fugiat nulla pariatur. Excepteur sint occaecat cupidatat non proident, sunt in culpa qui officia deserunt mollit anim id est laborum.</p>
  <div class="btn" style="left:111px;top:386px;width:149px;height:56px">Learn more</div>
  <div class="art" role="img" aria-label="Illustrated Pomeranian dog sitting on a soft pastel blob" style="left:695px;top:115px;width:360px;height:355px;border-radius:48% 52% 45% 55%;background:radial-gradient(circle at 45% 55%,#e6a96a,#ecd6c0 55%,#e3dccb)"></div>
</section>

<section class="buy">
  <div class="art" role="img" aria-label="Faint golden wave pattern" style="left:0;top:0;width:1200px;height:515px;background:linear-gradient(180deg,#e2d5b0,#e6dab7)"></div>
  <h2 class="abs script section-title" style="left:0;top:100px;width:1200px;text-align:center">How to buy our nft explanation</h2>
  <p class="abs buy-text">Lorem ipsum dolor sit amet, consectetur adipiscing elit, sed do eiusmod tempor incididunt ut labore et dolore magna aliqua. Ut enim ad minim veniam, quis nostrud exercitation ullamco laboris nisi ut aliquip ex ea commodo consequat. Duis aute irure dolor in reprehenderit in voluptate velit esse cillum dolore eu fugiat nulla pariatur. Excepteur sint occaecat cupidatat non proident, sunt in culpa qui officia deserunt mollit anim id est laborum.</p>
  <div class="btn" style="left:525px;top:356px;width:149px;height:56px">Learn more</div>
</section>
<div class="art" role="img" aria-label="Red and orange koi fish" style="left:980px;top:1440px;width:185px;height:280px;border-radius:50% 50% 45% 45%;background:linear-gradient(200deg,#f4f0ea 10%,#f2a23a 45%,#d8261c 85%);z-index:2"></div>

<section class="roadmap">
  <h2 class="abs script section-title" style="left:0;top:120px;width:1200px;text-align:center">Road map</h2>
  <div class="rail" style="left:149px;top:129px;height:143px"></div>
  <div class="rail" style="left:623px;top:489px;height:60px"></div>
  <div class="rail" style="left:623px;top:789px;height:65px"></div>
  <div class="rail" style="left:623px;top:1094px;height:60px"></div>

  <div class="card" style="left:110px;top:249px">
    <div class="diamond" style="left:34px;top:36px"></div>
    <span class="num" style="left:68px;top:32px">01.</span>
    <h3 style="left:106px;top:26px">Sed ut perspiciatis unde omnis iste natus error sit</h3>
    <p style="left:68px;top:110px">Lorem ipsum dolor sit amet, consectetur adipiscing elit, sed do eiusmod tempor incididunt ut labore et dolore magna aliqua. Ut enim ad minim veniam, quis nostrud exercitation ullamco laboris nisi ut aliquip ex ea commodo consequat.</p>
  </div>
  <div class="art" role="img" aria-label="Illustrated smiling Pomeranian dog" style="left:795px;top:207px;width:260px;height:260px;border-radius:45%;background:radial-gradient(circle,#e9a462,#f2c796 55%,rgba(249,238,208,0) 72%)"></div>

  <div class="art" role="img" aria-label="Illustrated grey Pekingese dog sitting" style="left:240px;top:535px;width:195px;height:250px;border-radius:40%;background:radial-gradient(circle,#7e6a58,#b8a58e 55%,rgba(249,238,208,0) 72%)"></div>
  <div class="card right" style="left:582px;top:549px">
    <div class="diamond" style="left:34px;top:36px"></div>
    <span class="num" style="left:68px;top:32px">02.</span>
    <h3 style="left:106px;top:26px">Sed ut perspiciatis unde omnis iste natus error sit</h3>
    <p style="left:68px;top:110px">Lorem ipsum dolor sit amet, consectetur adipiscing elit, sed do eiusmod tempor incididunt ut labore et dolore magna aliqua. Ut enim ad minim veniam, quis nostrud exercitation ullamco laboris nisi ut aliquip ex ea commodo consequat.</p>
  </div>

  <div class="card flip" style="left:110px;top:854px">
    <div class="diamond" style="left:509px;top:36px"></div>
    <span class="num" style="left:470px;top:32px">03.</span>
    <h3 style="left:80px;top:26px">Sed ut perspiciatis unde omnis iste natus error sit</h3>
    <p style="left:30px;top:110px">Lorem ipsum dolor sit amet, consectetur adipiscing elit, sed do eiusmod tempor incididunt ut labore et dolore magna aliqua. Ut enim ad minim veniam, quis nostrud exercitation ullamco laboris nisi ut aliquip ex ea commodo consequat.</p>
  </div>
  <div class="art" role="img" aria-label="Illustrated fluffy grey Pekingese dog" style="left:825px;top:860px;width:330px;height:265px;border-radius:45%;background:radial-gradient(circle,#6f6258,#aba096 55%,rgba(249,238,208,0) 72%)"></div>

  <div class="art" role="img" aria-label="Illustrated Pomeranian dog lying down" style="left:170px;top:1150px;width:335px;height:270px;border-radius:45%;background:radial-gradient(circle,#f0c08a,#f6dcc0 55%,rgba(249,238,208,0) 72%)"></div>
  <div class="card right" style="left:582px;top:1154px">
    <div class="diamond" style="left:34px;top:36px"></div>
    <span class="num" style="left:68px;top:32px">04.</span>
    <h3 style="left:106px;top:26px">Sed ut perspiciatis unde omnis iste natus error sit</h3>
    <p style="left:68px;top:110px">Lorem ipsum dolor sit amet, consectetur adipiscing elit, sed do eiusmod tempor incididunt ut labore et dolore magna aliqua. Ut enim ad minim veniam, quis nostrud exercitation ullamco laboris nisi ut aliquip ex ea commodo consequat.</p>
  </div>
</section>

<section class="faq">
  <div class="art" role="img" aria-label="Red ink painting of blossom trees and mountains" style="left:0;top:0;width:1200px;height:620px;background:radial-gradient(ellipse at 10% 40%,rgba(120,10,20,.35),rgba(0,0,0,0) 45%),radial-gradient(ellipse at 92% 70%,rgba(110,10,20,.4),rgba(0,0,0,0) 40%)"></div>
  <h2 class="abs script faq-title">Frequently asked questions</h2>
  <div class="faq-item" style="top:173px;height:130px"><h4 style="top:18px">What are SKULLS?</h4><span class="plus" style="top:14px">+</span><p>Lorem ipsum dolor sit amet, consectetur adipiscing elit, sed do eiusmod tempor incididunt ut labore et dolore magna aliqua.</p></div>
  <div class="faq-item" style="top:318px;height:68px"><h4 style="top:16px">What are SKULLS?</h4><span class="plus" style="top:12px">+</span></div>
  <div class="faq-item" style="top:403px;height:68px"><h4 style="top:16px">What are SKULLS?</h4><span class="plus" style="top:12px">+</span></div>
  <div class="faq-item" style="top:488px;height:68px"><h4 style="top:16px">What are SKULLS?</h4><span class="plus" style="top:12px">+</span></div>
</section>

<footer class="footer">
  <p class="abs footer-text">©Copyrights 2022 Lantern Paws &nbsp;&nbsp;| &nbsp;&nbsp;All Rights Reserved</p>
  <div class="abs social" style="left:955px;top:70px;gap:34px"><span style="width:16px;height:16px"></span><span style="width:16px;height:16px"></span><span style="width:16px;height:16px"></span></div>
</footer>

</body>
</html>
```